RTavenor Business Cards & Letterhead

I have a logo but need a design for some new business cards. We are a Design-Build Firm that specializes in the design and construction of commercial projects.
the cards need to be professional. no cartoon stuff.
i would like to have the cards in AI format so I can update the card as needed. Logo is provided.
Our Address is: 4187 Marlowe Ct. Maple Ridge, Ohio 27614

```html
<!DOCTYPE html>
<html lang="en">
<head>
<meta charset="utf-8">
<title>RTavenor Business Card</title>
<link rel="stylesheet" href="https://fonts.googleapis.com/css2?family=Open+Sans:wght@400;600;700;800&display=swap">
<style>
  :root {
    --backdrop: #333335;
    --card: #1f1f23;
    --card-deep: #18181b;
    --brand-grey: #76777b;
    --brand-blue: #1a73b8;
    --brand-blue-dark: #0f4f86;
    --ink-light: #ffffff;
  }
  * { box-sizing: border-box; margin: 0; padding: 0; }
  html, body {
    width: 1200px; height: 780px; overflow: hidden;
    background: var(--backdrop);
    font-family: "Open Sans", Arial, sans-serif;
  }
  .sheet {
    width: 1200px; height: 780px;
    display: flex; align-items: center; justify-content: center; gap: 40px;
  }
  .card {
    position: relative;
    width: 540px; height: 309px;
    background: var(--card);
    overflow: hidden;
    box-shadow: 0 10px 24px rgba(0,0,0,.45);
  }

  /* Back side: centred wordmark */
  .card--back { display: flex; align-items: center; justify-content: center; }
  .wordmark { display: flex; align-items: center; gap: 10px; }
  .wordmark__square { width: 34px; height: 34px; background: var(--brand-blue); }
  .wordmark__name {
    font-weight: 800; color: var(--brand-grey);
    font-size: 52px; letter-spacing: 1px; line-height: 1;
  }

  /* Front side */
  .card--front .wordmark { position: absolute; left: 34px; top: 34px; gap: 6px; }
  .card--front .wordmark__square { width: 20px; height: 20px; }
  .card--front .wordmark__name { font-size: 30px; }

  .edge-mark {
    position: absolute; right: -96px; top: 50%;
    transform: translateY(-50%) rotate(90deg);
    font-weight: 800; font-size: 52px; line-height: 1;
    color: var(--card-deep); letter-spacing: 1px; white-space: nowrap;
  }

  .identity {
    position: absolute; left: 0; top: 114px;
    display: flex; align-items: stretch;
  }
  .identity__bar {
    width: 22px;
    background: linear-gradient(180deg, var(--brand-blue-dark), var(--brand-blue));
  }
  .identity__text { padding-left: 12px; }
  .person-name {
    font-weight: 700; color: var(--brand-blue);
    font-size: 22px; letter-spacing: 1px; line-height: 1.1;
  }
  .person-role { font-weight: 700; color: var(--ink-light); font-size: 13px; margin-top: 2px; }

  .address {
    position: absolute; left: 34px; top: 184px;
    font-style: normal;
    color: var(--ink-light); font-size: 13px; line-height: 1.35;
  }
  .contacts {
    position: absolute; left: 34px; top: 228px;
    list-style: none; color: var(--ink-light); font-size: 13px; line-height: 1.35;
  }
  .contacts li { display: flex; align-items: center; gap: 8px; }
  .contacts svg { width: 12px; height: 12px; fill: var(--brand-blue); flex: none; }
</style>
</head>
<body>
<main class="sheet">
  <section class="card card--back" aria-label="Card back">
    <div class="wordmark">
      <span class="wordmark__square"></span>
      <span class="wordmark__name">RTAVENOR</span>
    </div>
  </section>

  <section class="card card--front" aria-label="Card front">
    <div class="wordmark">
      <span class="wordmark__square"></span>
      <span class="wordmark__name">RTAVENOR</span>
    </div>

    <span class="edge-mark" aria-hidden="true">RTAVENOR</span>

    <div class="identity">
      <span class="identity__bar"></span>
      <div class="identity__text">
        <p class="person-name">ROWAN TAVENOR</p>
        <p class="person-role">Founder/President</p>
      </div>
    </div>

    <address class="address">
      4187 Marlowe Ct. Maple Ridge,<br>Ohio 27614
    </address>

    <ul class="contacts">
      <li>
        <svg viewBox="0 0 24 24" aria-hidden="true"><path d="M6.6 10.8a15.1 15.1 0 0 0 6.6 6.6l2.2-2.2c.3-.3.7-.4 1-.2 1.1.4 2.3.6 3.6.6.6 0 1 .4 1 1V20c0 .6-.4 1-1 1A17 17 0 0 1 3 4c0-.6.4-1 1-1h3.5c.6 0 1 .4 1 1 0 1.3.2 2.5.6 3.6.1.3 0 .7-.2 1z"/></svg>
        (555) 555-0184
      </li>
      <li>
        <svg viewBox="0 0 24 24" aria-hidden="true"><path d="M12 2a10 10 0 1 0 0 20 10 10 0 0 0 0-20zm6.9 6h-2.9a15.6 15.6 0 0 0-1.4-3.6A8 8 0 0 1 18.9 8zM12 4c.8 1.2 1.5 2.5 1.9 4h-3.8c.4-1.5 1.1-2.8 1.9-4zM4.3 14a8.2 8.2 0 0 1 0-4h3.4a16.5 16.5 0 0 0 0 4zm.8 2h2.9c.3 1.3.8 2.5 1.4 3.6A8 8 0 0 1 5.1 16zM8 8H5.1a8 8 0 0 1 4.3-3.6C8.8 5.5 8.4 6.7 8 8zm4 12c-.8-1.2-1.5-2.5-1.9-4h3.8c-.4 1.5-1.1 2.8-1.9 4zm2.3-6H9.7a14.7 14.7 0 0 1 0-4h4.6a14.7 14.7 0 0 1 0 4zm.3 5.6c.6-1.1 1.1-2.3 1.4-3.6h2.9a8 8 0 0 1-4.3 3.6zm1.7-5.6a16.5 16.5 0 0 0 0-4h3.4a8.2 8.2 0 0 1 0 4z"/></svg>
        www.rtavenor.com
      </li>
      <li>
        <svg viewBox="0 0 24 24" aria-hidden="true"><path d="M3 5h18c.6 0 1 .4 1 1v12c0 .6-.4 1-1 1H3c-.6 0-1-.4-1-1V6c0-.6.4-1 1-1zm1 2.4V17h16V7.4l-8 5.3z M5.5 7 12 11.3 18.5 7z"/></svg>
        RT@RTavenor.com
      </li>
    </ul>
  </section>
</main>
</body>
</html>
```